Packaging label for Multi purpose ointment/balm

I would like to change packaging label (design) for multi purpose ointment (balm) that I have. Name of company is Ulo Tarvin and I named the product (ointment) KESTRIN. I attached pictures of existing label that i have (first file). The other 3 files are just changes that I was thinking to add. I would like to completely change look (design) of label. I was thinking to remove name KESTRIN and make it more stand out "multi purpose ointment" instead. But word KESTRIN can also stay on it if you think that would come out better. I was also thinking to change it to balm instead of ointment.
So I would like on label to stand out:
-multi purpose ointment or balm
-skin
-muscles
-joints
Ointment would be mostly use for skin problems, so I was thinking to add something like: cuts, burns, scrapes,... next to the word "skin".
Please feel free to use creation and completely change the look of label (design), because I want completely different design, and not similar design.
Here is description of multi purpose ointment:
Kestrin is multi purpose ointment with pain relief, anti-inflammatory and other healing properties for skin, muscles and joints. It is all natural, non-gmo, and made from the finest plant-based ingredients.
PURPOSE AND USE
Kestrin is a multi purpose ointment suitable for everyday use. It can be used to treat various injuries and phenomena of the skin such as wounds, sores, ulcers, mastitis, insect bites, burns, whitlow, herpes, aphthae, bruises, blisters and fungal infections with healing effects generally visible within 3 days. Do not apply directly on open wounds. It may be covered with a loosely wrapped sterile bandage that does not inhibit blood circulation. Kestrin also reduces swelling and relieves pain caused by rheumatism, gout, sciatica, arthritis. It can also be applied as a massage balm to improve blood circulation, reduce inflammation of muscles and ligaments, and alleviate back pain, joint pain, shoulder pain and other muscle soreness. For best results, massage affected area several times a day. In addition, the ointment can be used to effectively relieve nasal and upper respiratory congestion (apply around the nose, chest and throat). Kestrin may also be applied as a daily moisturizer to revitalize skin and prevent the formation of stretch marks. After use, the skin is soft and toned.
porvik Market(s)
Stores like brisk pantry, dellmart, porvik, hamblo, stores with natural products,...
Industry/Entity Type
It Company
Requirements
Nice to have
- I want completely different design. Not similar design.

```html
<!DOCTYPE html>
<html lang="en">
<head>
<meta charset="utf-8">
<title>Multi Purpose Ointment Label – Ulo Tarvin</title>
<link rel="stylesheet" href="https://fonts.googleapis.com/css2?family=Oswald:wght@500;600&family=Montserrat:wght@500;600&display=swap">
<style>
  :root {
    --page-bg: #f1f1f1;
    --label-light: #f7f8f8;
    --label-mid: #e2e6e7;
    --ring-outer: #c9cfd2;
    --ring-inner: #8e9598;
    --green-light: #4a8a1e;
    --green-dark: #2f5f17;
    --brand-green: #2e6b1f;
    --benefit-grey: #555859;
    --white: #ffffff;
  }
  * { margin: 0; padding: 0; box-sizing: border-box; }
  html, body {
    width: 1200px; height: 1200px; overflow: hidden;
    background: var(--page-bg);
  }
  .label {
    position: absolute; left: 0; top: 175px;
    width: 1200px; height: 850px; overflow: hidden;
    background: linear-gradient(90deg, var(--label-mid) 0%, var(--label-light) 30%, var(--label-light) 70%, var(--label-mid) 100%);
  }
  .label-rings { position: absolute; left: 0; top: 0; }
  .product-name {
    position: absolute; left: 0; width: 1200px; text-align: center;
    font-family: "Oswald", sans-serif; line-height: 1;
  }
  .product-name__line1 {
    top: 45px; font-size: 116px; font-weight: 600;
    color: var(--green-light); letter-spacing: -1px;
  }
  .product-name__line2 {
    top: 170px; font-size: 178px; font-weight: 600;
    color: var(--green-dark); letter-spacing: -2px;
  }
  .maker {
    position: absolute; left: 0; width: 1200px; text-align: center;
    font-family: "Montserrat", sans-serif;
  }
  .maker__by { top: 408px; font-size: 20px; font-weight: 500; color: var(--benefit-grey); }
  .maker__brand {
    top: 445px; display: flex; justify-content: center; align-items: center; gap: 12px;
    font-family: "Oswald", sans-serif; font-weight: 600; font-size: 44px; color: var(--brand-green);
  }
  .maker__mark { width: 30px; height: 30px; background: var(--brand-green); }
  .benefits {
    position: absolute; left: 0; top: 622px; width: 1200px;
    display: flex; justify-content: center; align-items: center; gap: 20px;
    font-family: "Montserrat", sans-serif; font-weight: 600; font-size: 70px;
    color: var(--benefit-grey); letter-spacing: -1px;
  }
  .benefits__dot { width: 20px; height: 20px; border-radius: 50%; background: var(--green-dark); }
  .volume-tab {
    position: absolute; left: 431px; top: 775px; width: 338px; height: 75px;
    background: linear-gradient(180deg, var(--green-light), var(--green-dark));
    border-radius: 20px 20px 0 0;
    display: flex; justify-content: center; align-items: center; gap: 38px;
    font-family: "Montserrat", sans-serif; font-weight: 600; font-size: 32px; color: var(--white);
  }
</style>
</head>
<body>
  <section class="label">
    <svg class="label-rings" width="1200" height="850" viewBox="0 0 1200 850" aria-hidden="true">
      <circle cx="600" cy="0" r="535" fill="none" stroke="var(--ring-outer)" stroke-width="10"/>
      <circle cx="600" cy="0" r="515" fill="none" stroke="var(--ring-inner)" stroke-width="4"/>
      <circle cx="600" cy="0" r="505" fill="var(--white)" fill-opacity="0.45"/>
    </svg>

    <h1>
      <span class="product-name product-name__line1">Multi Purpose</span>
      <span class="product-name product-name__line2">OINTMENT</span>
    </h1>

    <p class="maker maker__by">by</p>
    <p class="maker maker__brand"><span class="maker__mark"></span>Ulo Tarvin</p>

    <p class="benefits">
      <span>SKIN</span><span class="benefits__dot"></span>
      <span>MUSCLES</span><span class="benefits__dot"></span>
      <span>JOINTS</span>
    </p>

    <p class="volume-tab"><span>2.54 OZ.</span><span>75 ML</span></p>
  </section>
</body>
</html>
```